Velmarotix - world unique technology for better life - please let them know who am i at first sight

We need a new business card for company which is a provider of unique crystal based technology suitable for all living being. For more information and final design you can use our brochure (our colours are black and blue from brochure).
We use Verdana font

Industry/Entity Type

Business

Contact Information for Business Card

regular dimension

Font styles to use
Other font styles liked:
• Verdana

Requirements
Must have
• Logo
• name
• function/position
• phone
• mobile
• e-mail
• adress
Nice to have
• inovative design (technology directed)

```html
<!DOCTYPE html>
<html lang="en">
<head>
<meta charset="utf-8">
<title>Velmarotix – Business Card</title>
<link href="https://fonts.googleapis.com/css2?family=Exo+2:wght@600&family=Open+Sans:wght@400;600&display=swap" rel="stylesheet">
<style>
  :root {
    --page-bg: #e9ecef;
    --card-white: #ffffff;
    --card-shade: #eef0f2;
    --brand-blue: #2aa8e0;
    --swoosh-grey: #a7a9ac;
    --text-dark: #3a3a3a;
    --text-light: #ffffff;
  }
  * { margin: 0; padding: 0; box-sizing: border-box; }
  html, body {
    width: 1200px; height: 901px; overflow: hidden;
    background: var(--page-bg);
  }
  .business-card {
    position: absolute;
    left: 140px; top: 190px;
    width: 920px; height: 520px;
    border-radius: 48px;
    overflow: hidden;
    background: linear-gradient(160deg, var(--card-white) 0%, var(--card-shade) 100%);
    box-shadow: 0 10px 30px rgba(0,0,0,0.15);
  }
  .card-shapes { position: absolute; inset: 0; }
  .brand {
    position: absolute; left: 70px; top: 56px;
    display: flex; align-items: center; gap: 16px;
  }
  .brand-dot {
    width: 58px; height: 58px; border-radius: 50%;
    background: var(--brand-blue);
  }
  .brand-name {
    font-family: "Open Sans", sans-serif;
    font-weight: 400;
    font-size: 44px;
    letter-spacing: 2px;
    color: var(--brand-blue);
  }
  .holder { position: absolute; left: 70px; top: 176px; }
  .holder-name {
    font-family: "Exo 2", sans-serif;
    font-weight: 600; font-size: 27px; letter-spacing: 2px;
    color: var(--brand-blue);
  }
  .holder-role {
    font-family: "Open Sans", sans-serif;
    font-size: 19px; color: var(--text-dark); margin-top: 2px;
  }
  .contact-list {
    position: absolute; right: 48px; bottom: 40px;
    list-style: none; text-align: right;
    font-family: "Open Sans", sans-serif;
    font-size: 19px; color: var(--text-light);
  }
  .contact-list li {
    display: flex; justify-content: flex-end; align-items: center;
    gap: 12px; line-height: 34px;
  }
  .contact-icon { width: 20px; height: 20px; flex: none; }
</style>
</head>
<body>
  <div class="business-card">
    <svg class="card-shapes" viewBox="0 0 920 520" preserveAspectRatio="none" aria-hidden="true">
      <path class="swoosh-grey" fill="#a7a9ac" d="M0,218 C150,300 420,340 640,316 C430,352 170,330 0,262 Z"/>
      <path class="swoosh-blue" fill="#2aa8e0" d="M0,262 C170,335 430,372 640,336 C770,312 860,240 920,170 L920,520 L0,520 Z"/>
    </svg>

    <div class="brand">
      <span class="brand-dot"></span>
      <span class="brand-name">VELMAROTIX</span>
    </div>

    <div class="holder">
      <p class="holder-name">DANIEL KORVATH</p>
      <p class="holder-role">Managing Director</p>
    </div>

    <ul class="contact-list">
      <li>014 382 5067
        <svg class="contact-icon" viewBox="0 0 20 20"><rect x="5" y="1" width="10" height="18" rx="2" fill="none" stroke="#fff" stroke-width="1.6"/><circle cx="10" cy="15.5" r="1" fill="#fff"/></svg>
      </li>
      <li>014 382 5067
        <svg class="contact-icon" viewBox="0 0 20 20"><path d="M4 2 L8 2 L9 7 L6.5 8.5 C7.5 11 9 12.5 11.5 13.5 L13 11 L18 12 L18 16 C18 17 17 18 16 18 C8.5 17.5 2.5 11.5 2 4 C2 3 3 2 4 2 Z" fill="#fff"/></svg>
      </li>
      <li>info@velmarotix.com
        <svg class="contact-icon" viewBox="0 0 20 20"><rect x="1" y="4" width="18" height="12" fill="#fff"/><path d="M1 4 L10 11 L19 4" fill="none" stroke="#2aa8e0" stroke-width="1.4"/></svg>
      </li>
      <li>www.velmarotixlife.com
        <svg class="contact-icon" viewBox="0 0 20 20"><g fill="none" stroke="#fff" stroke-width="1.5"><circle cx="10" cy="10" r="8.5"/><ellipse cx="10" cy="10" rx="3.8" ry="8.5"/><path d="M1.5 10 H18.5 M3 5.5 H17 M3 14.5 H17"/></g></svg>
      </li>
      <li>027.9th floor,Harbor Crest Road KVN
        <svg class="contact-icon" viewBox="0 0 20 20"><path d="M10 1 C6 1 3.5 4 3.5 7.5 C3.5 12 10 19 10 19 C10 19 16.5 12 16.5 7.5 C16.5 4 14 1 10 1 Z" fill="#fff"/><circle cx="10" cy="7.5" r="2.5" fill="#2aa8e0"/></svg>
      </li>
    </ul>
  </div>
</body>
</html>
```